Printed Circuit Board Company Web Site Design - Please see new file 82012 web design

We are a printed circuit board manufacturer. Need a company professional web site to allow our potential customers to know more about our background, capability and our products. The web site will contain three languages, which are Chinese, English and Japanese. Our audience are mainly electronic companies that procure printed circuit boards. I have a word document that have all the required text in all three languages. The final design should communicate the impression that we embrace quality, trustworthiness and long term partnership business principles.
We should have sections that allow us to post pictures of our facilities.
I have added the three files in three different languages.
Some of the information is below:
Background
RDV Harbourline Limited (RDV) was set up in Hong Kong in 2007 by two Hong Kong entrepreneurs, Mr. Tak Wong and Mr. Lok Fai. We acquired the single sided printed circuit board factory located in Dongguan City, Guangdong Province, China, from Tovand Corporation of the U.S. in 2007. In addition to RDV, Mr. Wong and Mr. Fai also own Halberd Technology Company Limited, a semiconductor company based in Hong Kong since 1997 with a total investment of over US$100 million. Halberd is engaged in the manufacturing of flexible substrates and MEMS assembly business.
RDV has been awarded TS 16949 and ISO14000 certificates since 2009 and 2004 respectively.
Business Principles
RDV Harbourline Limited strives to be a professional top notched printed circuit board supplier. We embrace four “EXCELLENCE” principles, namely, excellence in quality, excellence in prices, excellence in services and excellence in on time delivery.
We approach each customer with a long-term partnership view that delivers the lowest ownership costs and highest total values to our customers. We customize quotations and solutions in order to allow our customers to win more businesses. We believe by thinking from our customers’ points of view we will be able to create a WIN-WIN relationship.
Customers
Due to our excellent quality, services and production systems, RDV Harbourline Limited manage to service a number of large Japanese and US customers, which include:
Technical capability overview
Below is an overview of our current capability:
Target Market(s)
Electronic companies buyers
Industry/Entity Type
Business
Requirements
Must have
- Capability description
Should not have
- no cartoon

```html
<!DOCTYPE html>
<html lang="en">
<head>
<meta charset="utf-8">
<title>RDV Harbourline Limited</title>
<link href="https://fonts.googleapis.com/css2?family=PT+Sans:ital,wght@0,400;0,700;1,400;1,700&family=Noto+Sans+SC:wght@400&display=swap" rel="stylesheet">
<style>
:root{
  --green:#138a5c;
  --green-dark:#0e7049;
  --ink:#3d3d3d;
  --text:#555;
  --muted:#777;
  --nav-dark:#474747;
  --page-grey:#efefef;
  --band-grey:#ececec;
  --footer:#585858;
  --btn:#2f2f2f;
  --bullet:#e0524f;
  --rule:#d6d6d6;
}
*{box-sizing:border-box;margin:0;padding:0}
html,body{width:960px;height:1200px;overflow:hidden}
body{font-family:"PT Sans",sans-serif;color:var(--text);position:relative;background:#fff}
.abs{position:absolute}
.bg-top{left:0;top:0;width:960px;height:248px;background:var(--page-grey)}
.bg-band{left:0;top:444px;width:960px;height:220px;background:linear-gradient(#e9e9e9,#fff)}
.bg-footer{left:0;top:1020px;width:960px;height:180px;background:var(--footer)}

.logo{left:104px;top:24px;width:240px;color:var(--green);font-weight:700;line-height:1}
.logo .mark{font-size:50px;letter-spacing:6px;display:block}
.logo .sub{font-size:19px;display:block;margin-top:4px;text-align:center}

.toplinks{left:571px;top:14px;font-size:11px;color:var(--muted)}
.toplinks span{margin:0 4px;color:#aaa}
.search{left:690px;top:13px;width:166px;height:19px;background:#fff;border:1px solid #ccc;border-radius:3px}
.search svg{position:absolute;right:5px;top:2px}
.call{right:104px;top:56px;font-size:17px;color:var(--ink)}
.call b{color:var(--green);font-weight:400;font-size:20px}

.nav{left:104px;top:110px;width:752px;height:33px;display:flex;background:var(--green);border-radius:3px;overflow:hidden}
.nav a{color:#fff;text-decoration:none;font-size:12px;display:flex;align-items:center;justify-content:center;border-right:1px solid #0b6a45;border-left:1px solid #22a06e}
.nav a.active{background:var(--nav-dark);border:none}

.slider{left:103px;top:150px;width:754px;height:310px;background:#fff;border:1px solid #d8d8d8;box-shadow:0 1px 3px rgba(0,0,0,.15)}
.slide{position:absolute;left:5px;top:5px;width:742px;height:298px;background:linear-gradient(100deg,#b9a3a2 0%,#d8d8d6 35%,#c6cbcc 70%,#8a8c90 100%)}
.dots{left:414px;top:460px;width:132px;height:24px}
.dots svg{display:block}

.news{left:104px;top:500px;width:752px;height:30px;background:#fff;border-radius:3px;display:flex;align-items:center;padding-left:22px;font-size:10px;color:var(--text);box-shadow:0 2px 3px rgba(0,0,0,.06)}
.news strong{font-weight:400;font-size:13px;color:var(--ink);margin-right:5px}
.news em{color:var(--green);margin-left:6px}
.news .more{margin-left:14px;color:#222;font-size:10px;font-weight:700}

h2{font-weight:400;font-size:20px;line-height:24px;color:var(--ink)}
h2 span{color:var(--green)}
.col p,.col li{font-size:9.6px;line-height:16px}
.btn{display:inline-block;background:var(--btn);color:#fff;font-size:10px;padding:0 9px;height:22px;line-height:22px;border-radius:2px}

.col1{left:104px;top:543px;width:240px}
.col1 .photo{margin-top:10px;width:240px;height:136px;border:2px solid #e4e4e4;background:linear-gradient(120deg,#8f9ea0,#d8dcdc 45%,#96a7b6)}
.col1 p{margin-top:13px;width:240px}

.col2{left:378px;top:555px;width:220px}
.col2 ul{list-style:none;margin-top:16px}
.col2 li{position:relative;padding-left:21px;margin-bottom:10px;line-height:12.5px}
.col2 li:before{content:"";position:absolute;left:2px;top:2px;width:7px;height:7px;border-radius:50%;background:var(--bullet)}

.col3{left:616px;top:543px;width:240px}
.quote{border-bottom:1px solid var(--rule);padding:8px 0 6px;margin-top:4px}
.quote p{text-indent:29px;position:relative}
.quote p svg{position:absolute;left:0;top:3px}
.quote .by{display:flex;justify-content:space-between;margin-top:10px;font-size:9.6px;color:#222}
.quote .by i{color:var(--green);font-weight:700}
.quote.last{border-bottom:none}

.b1{left:105px;top:864px}.b2{left:378px;top:864px}.b3{left:616px;top:864px}
.divider{left:0;top:904px;width:960px;height:1px;background:#e6e6e6}

.clients-h{left:104px;top:912px}
.arrows{left:820px;top:946px}
.clients{left:104px;top:972px;width:752px;height:94px;background:#fff;border:1px solid #ccc;border-radius:3px;display:flex;align-items:center;overflow:hidden}
.clients .cat{width:82px;height:100%;background:linear-gradient(90deg,#f2f2f2,#e6e6e6);display:flex;align-items:center;justify-content:center;text-align:center;font-size:14px;line-height:17px;color:var(--ink);font-weight:700;box-shadow:2px 0 4px rgba(0,0,0,.12)}
.clients .cn{font-family:"Noto Sans SC","PT Sans",sans-serif;font-size:38px;color:#9a9a9a;margin-left:32px;letter-spacing:1px}
.clients .name{font-size:16px;color:#666;font-weight:700;display:flex;align-items:center;gap:6px}
.clients .name i{display:inline-block;width:10px;height:10px;border-radius:50%;background:#999}

.fnav{left:104px;top:1080px;font-size:9.6px;line-height:16.1px;color:#eee}
.social{left:296px;top:1080px}
.social div{display:flex;align-items:center;height:30px;font-size:9.6px;color:#ddd}
.social i{display:inline-block;width:16px;height:16px;border-radius:3px;background:#7c8894;margin-right:11px}
.newsletter{left:424px;top:1077px;color:#fff;font-size:13px}
.field{left:424px;top:1103px;width:176px;height:20px;background:#2e2e2e;border-radius:4px;color:#aaa;font-size:9px;font-style:italic;padding:4px 7px}
.submit{left:548px;top:1132px;width:52px;height:20px;background:var(--green);border-radius:2px;color:#fff;font-size:11px;text-align:center;line-height:20px}
.flogo{left:652px;top:1078px;width:204px;height:64px;background:#fff;color:var(--green);font-weight:700;text-align:center;padding-top:6px;line-height:1}
.flogo .mark{font-size:30px;letter-spacing:4px;display:block}
.flogo .sub{font-size:12px;display:block;margin-top:3px}
.copy{left:652px;top:1153px;font-size:9.6px;line-height:16px;color:#eee}
</style>
</head>
<body>
<div class="abs bg-top"></div>
<div class="abs bg-band"></div>
<div class="abs bg-footer"></div>

<header>
  <div class="abs logo"><span class="mark">RDV</span><span class="sub">Harbourline Limited</span></div>
  <div class="abs toplinks">Home<span>|</span>FAQ<span>|</span>Site Map</div>
  <div class="abs search"><svg width="14" height="14" viewBox="0 0 14 14"><circle cx="5.5" cy="5.5" r="4" fill="none" stroke="#aaa" stroke-width="1.6"/><line x1="8.5" y1="8.5" x2="13" y2="13" stroke="#aaa" stroke-width="2"/></svg></div>
  <div class="abs call">Call Us : <b>(852)30450162</b></div>
  <nav class="abs nav">
    <a class="active" style="width:88px">About Us</a>
    <a style="width:90px">Services</a>
    <a style="width:168px">Technical Specifications</a>
    <a style="width:85px">Clients</a>
    <a style="width:114px">Testimonials</a>
    <a style="width:115px">News &amp; Events</a>
    <a style="width:92px">Contact Us</a>
  </nav>
</header>

<section class="abs slider">
  <div class="slide" role="img" aria-label="Photo of the printed circuit board production line equipment in the factory"></div>
</section>
<div class="abs dots">
  <svg width="132" height="24" viewBox="0 0 132 24"><path d="M0 0H132L125 24H7Z" fill="#4a4a4a"/>
    <circle cx="24" cy="12" r="6" fill="var(--green)"/><circle cx="45" cy="12" r="6" fill="#fff"/><circle cx="66" cy="12" r="6" fill="#fff"/><circle cx="86" cy="12" r="6" fill="#fff"/><circle cx="106" cy="12" r="6" fill="#fff"/></svg>
</div>

<div class="abs news"><strong>Update News :</strong> Aliquam ullamcorper tempor felis, nec condimentum odio aliquet vitae. Morbi iaculis fringilla gravida. <em>On Aug 20, 2012.</em><span class="more">Read More &gt;&gt;</span></div>

<section class="abs col col1">
  <h2>Welcome to<br><span>RDV Harbourline Limited</span></h2>
  <div class="photo" role="img" aria-label="Photo of engineers working at factory testing machines"></div>
  <p>RDV Harbourline Limited (RDV) was set up in Hong Kong in 2007 by two Hong Kong entrepreneurs, Mr. Tak Wong and Mr. Lok Fai. We acquired the single sided printed circuit board factory located in Dongguan City, Guangdong Province, China, from Tovand Corporation of the U.S. in 2007.</p>
</section>

<section class="abs col col2">
  <h2>Our <span>Services</span></h2>
  <ul>
    <li>Lorem ipsum dolor sit amet.</li>
    <li>Fusce accumsan elit a suscipit sagittis.</li>
    <li>Nam fermentum vestibulum purus id aliquet.</li>
    <li>Vestibulum vel metus sit amet turpis bibendum.</li>
    <li>Nunc consequat congue nulla eu imperdiet.</li>
    <li>Lorem ipsum dolor sit amet.</li>
    <li>Fusce accumsan elit a suscipit sagittis.</li>
    <li>Nam fermentum vestibulum purus id aliquet.</li>
  </ul>
</section>

<section class="abs col col3">
  <h2>What<br><span>Customers Says</span></h2>
  <div class="quote"><p><svg width="22" height="11" viewBox="0 0 22 11"><g fill="#aaa"><circle cx="5" cy="6" r="5"/><path d="M1 5Q2 0 7 0L6 2Q3 2 3 5Z"/><circle cx="16" cy="6" r="5"/><path d="M12 5Q13 0 18 0L17 2Q14 2 14 5Z"/></g></svg>Duis aute irure dolor in reprehenderit in voluptate velit esse cillum dolore euugiat nulla pariatur......</p><div class="by"><span>Read More</span><i>Alan Morrow</i></div></div>
  <div class="quote"><p><svg width="22" height="11" viewBox="0 0 22 11"><g fill="#aaa"><circle cx="5" cy="6" r="5"/><path d="M1 5Q2 0 7 0L6 2Q3 2 3 5Z"/><circle cx="16" cy="6" r="5"/><path d="M12 5Q13 0 18 0L17 2Q14 2 14 5Z"/></g></svg>Duis aute irure dolor in reprehenderit in voluptate velit esse cillum dolore euugiat nulla pariatur......</p><div class="by"><span>Read More</span><i>Alan Morrow</i></div></div>
  <div class="quote last"><p><svg width="22" height="11" viewBox="0 0 22 11"><g fill="#aaa"><circle cx="5" cy="6" r="5"/><path d="M1 5Q2 0 7 0L6 2Q3 2 3 5Z"/><circle cx="16" cy="6" r="5"/><path d="M12 5Q13 0 18 0L17 2Q14 2 14 5Z"/></g></svg>Duis aute irure dolor in reprehenderit in voluptate velit esse cillum dolore euugiat nulla pariatur......</p><div class="by"><span>Read More</span><i>Alan Morrow</i></div></div>
</section>

<span class="abs btn b1">Read More</span>
<span class="abs btn b2">Read More</span>
<span class="abs btn b3">Read More</span>
<div class="abs divider"></div>

<section>
  <h2 class="abs clients-h">Our<br><span>Valuable Clients</span></h2>
  <svg class="abs arrows" width="32" height="16" viewBox="0 0 32 16"><path d="M9 2L3 8L9 14M23 2L29 8L23 14" fill="none" stroke="#222" stroke-width="2.2"/></svg>
  <div class="abs clients">
    <div class="cat">Auto<br>Motive</div>
    <span class="cn">主要客户群</span>
    <span class="name" style="margin-left:44px"><i></i>Vantrel</span>
    <span class="name" style="margin-left:50px"><i></i>Korimo Motor</span>
    <span class="name" style="margin-left:50px">Brenzel</span>
  </div>
</section>

<footer>
  <div class="abs fnav">About Us<br>Services<br>Technical Specifications<br>Clients<br>Testimonials<br>News &amp; Events<br>Contact Us</div>
  <div class="abs social">
    <div><i></i>Linkbook</div>
    <div><i></i>Chirper</div>
    <div><i></i>Circlenet</div>
    <div><i style="background:#d9772c"></i>Rss Feeds</div>
  </div>
  <div class="abs newsletter">Newsletter Sign Up</div>
  <div class="abs field">enter email address</div>
  <div class="abs submit">Submit</div>
  <div class="abs flogo"><span class="mark">RDV</span><span class="sub">Harbourline Limited</span></div>
  <div class="abs copy">Copyright © 2012All Rights Reserved<br>Privacy Policy</div>
</footer>
</body>
</html>
```